Computer Repair Business - Needs New Business Card Design

I want to create a very cool business card for my business. I want to make it 100% different from my previous card. I would like to use similar color scheme like Royal blue.

With this card I want to create a conversation and have my customers say "Wow, that's a cool business card" Trying to prevent it from looking like the typical card that get's shoved into a wallet.

My website is below:

www.lornapcfix.com

I want to edit the hours and website and email:

www.lornapcfix.com
lorna@lornapcfix.com

10:30 to 6pm Monday - Friday
10:30 to 3pm Saturday
Updates

Just to remind, when i see a new design i don't want to notice my old design.

Business card will be printed and made with rounded corners and horizontal.

The back of the card should say " In-Store Repair, Remote Support, Data Recovery"

Industry/Entity Type

Business

Font styles to use
Sans Serif

Colors
33a6d7
3176b5

Requirements
Must have
• Clean looking - have creative aspects.
Should not have
• Should not look like the previous card design.

```html
<!DOCTYPE html>
<html lang="en">
<head>
<meta charset="utf-8">
<title>Lorna PC Fix – Business Card</title>
<link rel="stylesheet" href="https://fonts.googleapis.com/css2?family=Open+Sans:wght@400;600;700&display=swap">
<style>
  :root {
    --royal: #1f5fb8;
    --royal-deep: #174a96;
    --sky: #33a6d7;
    --ink: #2b2b2b;
    --ink-soft: #555;
    --paper: #ffffff;
    --paper-shade: #eef0f2;
    --stage: #e6e8eb;
  }
  * { margin: 0; padding: 0; box-sizing: border-box; }
  html, body {
    width: 1200px; height: 899px; overflow: hidden;
    background: var(--stage);
    font-family: "Open Sans", Arial, sans-serif;
  }
  .stage {
    position: relative; width: 1200px; height: 899px;
    display: flex; align-items: center; justify-content: center; gap: 40px;
  }
  .card {
    position: relative; width: 540px; height: 308px;
    border-radius: 30px; overflow: hidden;
    box-shadow: 0 10px 30px rgba(0,0,0,.18);
  }
  /* Front */
  .card-front { background: linear-gradient(160deg, var(--paper) 55%, var(--paper-shade)); }
  .card-front .swoosh { position: absolute; left: 0; bottom: 0; width: 540px; height: 140px; }
  .brand {
    position: absolute; left: 38px; top: 78px;
    display: flex; align-items: center; gap: 12px;
  }
  .brand-square { width: 26px; height: 26px; background: var(--royal); }
  .brand-name {
    font-weight: 600; font-size: 30px; letter-spacing: 1px;
    color: var(--ink);
  }
  .person { position: absolute; left: 302px; top: 38px; }
  .person-name { font-weight: 700; font-size: 15px; color: var(--royal); letter-spacing: .5px; }
  .person-title { font-size: 10px; color: var(--ink); margin-top: 1px; }
  .address { position: absolute; left: 302px; top: 104px; font-size: 13px; line-height: 1.5; color: var(--ink); }
  .contacts { position: absolute; left: 302px; top: 172px; list-style: none; font-size: 9.5px; color: var(--ink); }
  .contacts li { display: flex; align-items: center; gap: 8px; height: 17px; }
  .contacts svg { width: 10px; height: 10px; fill: var(--royal); }
  .front-web {
    position: absolute; right: 34px; bottom: 20px;
    font-size: 13px; color: var(--paper); letter-spacing: .2px;
  }
  /* Back */
  .card-back { background: linear-gradient(180deg, var(--royal) 0%, var(--royal-deep) 100%); color: var(--paper); }
  .services { position: absolute; left: 0; top: 52px; width: 100%; display: flex; justify-content: space-around; list-style: none; padding: 0 30px; }
  .service { width: 130px; text-align: center; }
  .service svg { width: 44px; height: 44px; margin-bottom: 12px; }
  .service-label { font-size: 14px; line-height: 1.25; font-weight: 400; }
  .hours {
    position: absolute; left: 0; right: 0; top: 196px;
    text-align: center; font-size: 11px; line-height: 1.6; opacity: .95;
  }
  .back-web { position: absolute; left: 0; right: 0; bottom: 26px; text-align: center; font-size: 13px; font-weight: 600; letter-spacing: .5px; }
</style>
</head>
<body>
<main class="stage">
  <section class="card card-front" aria-label="Card front">
    <svg class="swoosh" viewBox="0 0 540 140" preserveAspectRatio="none" aria-hidden="true">
      <path d="M0 20 C120 80 260 95 540 70 L540 140 L0 140 Z" fill="var(--ink)"/>
      <path d="M0 34 C130 92 270 104 540 80 L540 140 L0 140 Z" fill="var(--royal)"/>
    </svg>
    <div class="brand">
      <span class="brand-square"></span>
      <span class="brand-name">LORNA PC FIX</span>
    </div>
    <div class="person">
      <p class="person-name">MARK ELLISON</p>
      <p class="person-title">Managing Director</p>
    </div>
    <p class="address">112 Maple Ave,<br>Riverton, NJ 08077</p>
    <ul class="contacts">
      <li><svg viewBox="0 0 10 10"><path d="M2 0h2l1 2.5-1.3 1a6 6 0 0 0 2.8 2.8l1-1.3L10 6v2a2 2 0 0 1-2 2A8 8 0 0 1 0 2a2 2 0 0 1 2-2z"/></svg>555.201.4478</li>
      <li><svg viewBox="0 0 10 10"><path d="M0 2h10v6H0z"/><path d="M0 2l5 3.5L10 2" fill="none" stroke="#fff" stroke-width="1"/></svg>lorna@lornapcfix.com</li>
      <li><svg viewBox="0 0 10 10"><circle cx="5" cy="5" r="5"/><path d="M0 5h10M5 0c-2.5 3-2.5 7 0 10M5 0c2.5 3 2.5 7 0 10" fill="none" stroke="#fff" stroke-width=".7"/></svg>www.lornapcfix.com</li>
    </ul>
    <p class="front-web">www.lornapcfix.com</p>
  </section>

  <section class="card card-back" aria-label="Card back">
    <ul class="services">
      <li class="service">
        <svg viewBox="0 0 44 44" aria-hidden="true"><rect x="6" y="10" width="32" height="20" rx="2" fill="none" stroke="#fff" stroke-width="2.5"/><path d="M16 36h12M22 30v6" stroke="#fff" stroke-width="2.5"/></svg>
        <p class="service-label">In-Store<br>Repair</p>
      </li>
      <li class="service">
        <svg viewBox="0 0 44 44" aria-hidden="true"><circle cx="22" cy="22" r="15" fill="none" stroke="#fff" stroke-width="2.5"/><path d="M7 22h30M22 7c-7 8-7 22 0 30M22 7c7 8 7 22 0 30" fill="none" stroke="#fff" stroke-width="2"/></svg>
        <p class="service-label">Remote<br>Support</p>
      </li>
      <li class="service">
        <svg viewBox="0 0 44 44" aria-hidden="true"><rect x="10" y="10" width="24" height="24" rx="2" fill="#fff"/><rect x="16" y="16" width="12" height="12" fill="var(--royal)"/></svg>
        <p class="service-label">Data<br>Recovery</p>
      </li>
    </ul>
    <p class="hours">Mon – Fri 10:30 am – 6:00 pm / Sat 10:30 am – 3:00 pm<br>Sunday by appointment</p>
    <p class="back-web">www.lornapcfix.com</p>
  </section>
</main>
</body>
</html>
```